plumbers buisness card

A buisness card for a plumbing buisness
needs to have a water theme with navy blue, light blue and white
with an image of either a water drop, pipes, tools or something relating to plumbing and incorperating my buisness name as a logo

"Kettering Plumbing" is the words that need to stand out with "& gasfitting" to be smaller

spelling error on brief, "maintenance"
and also could you include my email d_kettering@mailwave.com.au

Industry/Entity Type

Plumbing

Contact Information for Business Card

Kettering Plumbing & Gasfitting

declan kettering
0432961085

specialising in
-new homes
-maitenance
-renovations

license no.
-73840

```html
<!DOCTYPE html>
<html lang="en">
<head>
<meta charset="UTF-8">
<title>Kettering Plumbing &amp; Gasfitting — Business Card</title>
<link rel="stylesheet" href="https://fonts.googleapis.com/css2?family=Lexend+Exa:wght@700;800&display=swap">
<style>
  :root {
    --card-bg: #e3eaf2;
    --brand-blue: #0a7fbb;
    --text-grey: #5a5b5d;
    --water-light: #1993c8;
    --water-mid: #0b84bf;
    --water-deep: #0566a2;
  }
  html, body {
    margin: 0;
    padding: 0;
    width: 1200px;
    height: 741px;
    overflow: hidden;
    background: var(--card-bg);
  }
  .card {
    position: relative;
    width: 1200px;
    height: 741px;
    background: var(--card-bg);
    font-family: "Lexend Exa", "Arial Black", sans-serif;
    text-transform: uppercase;
    overflow: hidden;
  }
  .brand {
    position: absolute;
    left: 130px;
    top: 196px;
    display: flex;
    flex-direction: column;
    align-items: flex-end;
    line-height: 1;
  }
  .brand-name {
    font-size: 38px;
    font-weight: 800;
    letter-spacing: -0.5px;
    color: var(--brand-blue);
  }
  .brand-trade {
    margin-top: 14px;
    font-size: 24px;
    font-weight: 800;
    letter-spacing: 0;
    color: var(--text-grey);
  }
  .contact {
    position: absolute;
    left: 128px;
    top: 388px;
  }
  .contact-name {
    margin: 0;
    font-size: 40px;
    font-weight: 800;
    line-height: 1.15;
    letter-spacing: -0.5px;
    color: var(--brand-blue);
  }
  .contact-line {
    margin: 4px 0 0;
    font-size: 22px;
    font-weight: 800;
    line-height: 1.35;
    letter-spacing: -0.3px;
    color: var(--text-grey);
  }
  .contact-line .divider {
    color: var(--brand-blue);
    margin: 0 14px;
  }
  .contact-email {
    margin-top: 2px;
  }
  .services {
    position: absolute;
    left: 128px;
    top: 562px;
    margin: 0;
    font-size: 22px;
    font-weight: 700;
    letter-spacing: -0.5px;
    color: var(--brand-blue);
  }
  .services .divider {
    color: var(--text-grey);
    margin: 0 10px;
  }
  .water-band {
    position: absolute;
    left: 0;
    top: 637px;
    width: 1200px;
    height: 104px;
    background:
      radial-gradient(ellipse 260px 60px at 20% 40%, rgba(255,255,255,0.10), transparent 70%),
      radial-gradient(ellipse 300px 70px at 75% 55%, rgba(255,255,255,0.08), transparent 70%),
      linear-gradient(100deg, var(--water-light) 0%, var(--water-mid) 50%, var(--water-deep) 100%);
  }
</style>
</head>
<body>
  <main class="card">
    <div class="brand">
      <span class="brand-name">Kettering Plumbing</span>
      <span class="brand-trade">&amp; Gasfitting</span>
    </div>

    <section class="contact">
      <h1 class="contact-name">Declan Kettering</h1>
      <p class="contact-line">0432961085<span class="divider">I</span>License No. 73840</p>
      <p class="contact-line contact-email">d_kettering@mailwave.com.au</p>
    </section>

    <p class="services">New Homes<span class="divider">I</span>Maintenance<span class="divider">I</span>Renovations</p>

    <div class="water-band" role="img" aria-label="Close-up photo of blue water droplets"></div>
  </main>
</body>
</html>
```